KRWB new business card design

We need a business card design for our established business which is Australia wide however based in Melbourne. We are a young team of Financial Planners who specialize in Insurance and Basic super advice for people like us.

We are people who help our clients get things done in a timely and cost effective manner whilst having a good time and a laugh along the way.

We would like this to have a consistent feel with our new e-brochure which i have attached from a color and font perspective.

Industry/Entity Type

Business

Requirements
Must have
• We do not need specific address details rather just the states we are in:

VIC/NSW/QLD/TAS
Nice to have
• Curved edge to mate the brochure

```html
<!DOCTYPE html>
<html lang="en">
<head>
<meta charset="utf-8">
<title>KRWB business card</title>
<link href="https://fonts.googleapis.com/css2?family=Arimo:ital,wght@0,400;0,700;1,700&family=PT+Sans&display=swap" rel="stylesheet">
<style>
  :root {
    --stage: #e8e3dc;
    --label: #2a2a2a;
    --white: #ffffff;
    --green: #6cbf4e;
    --green-dark: #0fa04a;
    --grey-text: #6b6b6b;
    --dark-text: #333333;
    --black-card: #141414;
    --faint: #eef1ec;
  }
  * { box-sizing: border-box; margin: 0; padding: 0; }
  html, body { width: 1200px; height: 788px; overflow: hidden; }
  body {
    position: relative;
    background: var(--stage);
    font-family: "Arimo", Arial, sans-serif;
  }
  .side-label {
    position: absolute;
    width: 525px;
    text-align: center;
    font-family: "PT Sans", sans-serif;
    font-size: 22px;
    color: var(--label);
  }
  .card {
    position: absolute;
    width: 525px;
    height: 300px;
    border-radius: 22px;
    overflow: hidden;
    background: var(--white);
  }
  .brand {
    position: absolute;
    display: flex;
    align-items: center;
    gap: 10px;
    font-weight: 700;
    color: var(--green-dark);
    white-space: nowrap;
  }
  .brand-square { background: var(--green); border-radius: 6px; flex: none; }

  /* Front */
  .front { left: 53px; top: 72px; }
  .front .swoosh { position: absolute; inset: 0; }
  .front .brand { left: 60px; top: 104px; font-size: 42px; }
  .front .brand-square { width: 32px; height: 32px; }
  .states {
    position: absolute; left: 60px; bottom: 18px;
    font-size: 13px; color: var(--dark-text);
  }
  .contact {
    position: absolute; right: 20px; top: 92px;
    text-align: right; color: var(--white);
  }
  .contact-name { font-size: 16px; font-weight: 700; line-height: 20px; }
  .contact-role { font-size: 13px; font-weight: 700; line-height: 18px; }
  .contact-lines { margin-top: 18px; font-size: 13.5px; line-height: 24px; }
  .contact-lines dt { display: inline; font-style: italic; font-weight: 700; }
  .contact-lines dd { display: inline; }

  /* Services lists */
  .services-title { font-style: italic; font-weight: 700; font-size: 17px; }
  .services { list-style: none; font-weight: 700; font-size: 14px; }
  .services li::before { content: "▪ "; font-size: 11px; }

  /* Back 1 */
  .back-one { left: 622px; top: 74px; }
  .back-one .brand { left: 62px; top: 110px; font-size: 38px; }
  .back-one .brand-square { width: 30px; height: 30px; }
  .back-one .divider {
    position: absolute; left: 261px; top: 20px; width: 2px; height: 235px;
    background: linear-gradient(var(--white), #9a9a9a, var(--white));
  }
  .back-one .services-block { position: absolute; left: 320px; top: 45px; color: var(--grey-text); }
  .back-one .services { margin-top: 12px; }
  .back-one .services li { line-height: 34px; }
  .tag-band {
    position: absolute; left: 0; right: 0; bottom: 0; height: 39px;
    background: var(--green); color: var(--white);
    font-size: 14px; font-weight: 700; text-align: center; line-height: 39px;
  }

  /* Back 2 */
  .back-two { left: 53px; top: 446px; }
  .back-two .ghost {
    position: absolute; left: 152px; top: 12px; width: 225px; height: 285px;
    border-radius: 30px; background: var(--faint);
  }
  .back-two .services-block {
    position: absolute; left: 0; right: 0; top: 45px;
    text-align: center; color: var(--dark-text);
  }
  .back-two .services { margin-top: 12px; }
  .back-two .services li { line-height: 34px; }
  .back-two .tagline {
    position: absolute; left: 0; right: 0; bottom: 16px;
    text-align: center; font-size: 14px; font-weight: 700; color: var(--dark-text);
  }

  /* Back 3 */
  .back-three { left: 622px; top: 446px; background: var(--black-card); }
  .back-three .texture {
    position: absolute; inset: 0;
    background: radial-gradient(circle at 35% 40%, #2e2e2e, #101010 75%);
  }
  .back-three .brand { left: 62px; top: 116px; font-size: 52px; color: var(--white); }
  .back-three .brand-square { width: 40px; height: 40px; }
  .back-three .services-block { position: absolute; left: 314px; top: 24px; color: var(--white); }
  .back-three .services { margin-top: 12px; }
  .back-three .services li { line-height: 34px; }
  .back-three .tagline {
    position: absolute; left: 313px; top: 254px;
    font-size: 14px; font-weight: 700; line-height: 18px; color: var(--green);
  }
</style>
</head>
<body>
  <div class="side-label" style="left:53px; top:32px;">Front</div>
  <div class="side-label" style="left:622px; top:32px;">Back - 1</div>
  <div class="side-label" style="left:53px; top:402px;">Back - 2</div>
  <div class="side-label" style="left:622px; top:402px;">Back - 3</div>

  <section class="card front">
    <svg class="swoosh" width="525" height="300" viewBox="0 0 525 300" aria-hidden="true">
      <path d="M392 0 H525 V300 H252 C330 220 372 130 392 0 Z" fill="var(--green)"/>
      <path d="M378 0 H387 C366 132 324 222 248 300 H240 C314 222 356 132 378 0 Z" fill="var(--green-dark)"/>
    </svg>
    <div class="brand"><span class="brand-square"></span>KRWB</div>
    <p class="states">VIC/NSW/QLD/TAS</p>
    <div class="contact">
      <p class="contact-name">Daniel Hartley</p>
      <p class="contact-role">ADFS, BBus, LRS©</p>
      <p class="contact-role">Financial Adviser</p>
      <dl class="contact-lines">
        <div><dt>cell</dt> <dd>0400 555 214</dd></div>
        <div><dt>phone</dt> <dd>1300 555 418</dd></div>
        <div><dt>fax</dt> <dd>03 9555 0172</dd></div>
        <div><dt>email</dt> <dd>daniel@krwb.com.au</dd></div>
        <div><dt>web</dt> <dd>www.krwb.com.au</dd></div>
      </dl>
    </div>
  </section>

  <section class="card back-one">
    <div class="brand"><span class="brand-square"></span>KRWB</div>
    <div class="divider"></div>
    <div class="services-block">
      <p class="services-title">Specialising in</p>
      <ul class="services">
        <li>Risk Insurance</li>
        <li>Debt Management</li>
        <li>Superannuation</li>
        <li>Wealth Creation</li>
        <li>Retirement Planning</li>
      </ul>
    </div>
    <p class="tag-band">SECURE FUTURE, ENHANCED LIFESTYLE</p>
  </section>

  <section class="card back-two">
    <div class="ghost"></div>
    <div class="services-block">
      <p class="services-title">Specialising in</p>
      <ul class="services">
        <li>Risk Insurance</li>
        <li>Debt Management</li>
        <li>Superannuation</li>
        <li>Wealth Creation</li>
        <li>Retirement Planning</li>
      </ul>
    </div>
    <p class="tagline">SECURE FUTURE, ENHANCED LIFESTYLE</p>
  </section>

  <section class="card back-three">
    <div class="texture" role="img" aria-label="Dark metallic mesh texture background"></div>
    <div class="brand"><span class="brand-square"></span>KRWB</div>
    <div class="services-block">
      <p class="services-title">Specialising in</p>
      <ul class="services">
        <li>Risk Insurance</li>
        <li>Debt Management</li>
        <li>Superannuation</li>
        <li>Wealth Creation</li>
        <li>Retirement Planning</li>
      </ul>
    </div>
    <p class="tagline">SECURE FUTURE<br>ENHANCED LIFESTYLE</p>
  </section>
</body>
</html>
```